Digital Marketing Website Redesign, modern, fresh, dynamic

Hi there, we would like to freshen up our website and create a new dynamic look. We are a digital marketing agency who specialise in digital transformation in the form of creating websites for appointment bookings. Our clients are service businesses such as hairdressers, dentists and doctors who's patients need to book appointments with them.

Our company name is Tallomex with the point being we can help increase your revenue curve by increasing your appointment bookings.

Our services include building the website, creating campaigns to drive traffic, increasing conversions and monitoring and reporting.

We are playing with a tagline of 'Step into your Digital Transformation' as we have a 5 step journey that customers can take with us getting them from zero to full appointment bookings.

Our current website is www.tallomex-sample.com

You can see a draft design that I mocked up on Canva here https://www.draftboard-sample.com/design/QXB82LmpR7T/KpoW39dnFsYbZet_wqe_OPa/edit?utm_content=QXB82LmpR7T&utm_campaign=designshare&utm_medium=link2&utm_source=sharebutton

Also attached some other homepage ideas. In regard to photos we are open to ideas.

Please let if you need any more information to provide us with an initial design. Thanks million and I look forward to receiving fantastic designs :)

Marian Dobbs
Tallomex

Target Market(s)

Appointment based businesses such as hairdressers, dentists, doctors

Industry/Entity Type

Marketing and Digital

Coding

Coded - Design and coding required

Number of Pages Required

1 page

Colors
0094D4
00A9DD
6FCCEA
C7EBF8
E9F6FB

Requirements
Must have
• Appointment booking CTA
Nice to have
• A website we like https://www.fergalwhitty-sample.ie

```html
<!DOCTYPE html>
<html lang="en">
<head>
<meta charset="utf-8">
<title>Tallomex – Step Into Your Digital Transformation</title>
<link href="https://fonts.googleapis.com/css2?family=Montserrat:wght@600;700;800&family=Roboto:wght@400;500;700&display=swap" rel="stylesheet">
<style>
:root{
  --blue:#3a6cb6;
  --blue-deep:#2c4f8c;
  --navy:#142a55;
  --green:#a9b518;
  --pale:#eceed3;
  --ring:#dcdcd4;
  --ink:#2b2b2b;
  --muted:#555a60;
  --white:#ffffff;
}
*{box-sizing:border-box;margin:0;padding:0}
html,body{width:1200px;height:3877px;overflow:hidden;background:var(--white)}
body{font-family:"Roboto",Arial,sans-serif;color:var(--ink)}
.page{position:relative;width:1200px;height:3877px;overflow:hidden}
.abs{position:absolute}
.deco{position:absolute;left:0;top:0;width:1200px;height:3877px}

/* header */
.header{position:absolute;left:0;top:0;width:1200px;height:90px;background:var(--white);z-index:3}
.logo-disc{position:absolute;left:140px;top:-100px;width:254px;height:256px;border-radius:50%;background:var(--white);z-index:4}
.logo{position:absolute;left:140px;width:254px;top:44px;text-align:center;z-index:5;font-family:"Montserrat",sans-serif;font-weight:800;font-size:36px;color:var(--blue);letter-spacing:.3px}
.nav{position:absolute;top:36px;left:417px;z-index:5;font-size:12.5px;font-weight:500;color:#222}
.nav a{color:#222;text-decoration:none;position:absolute;white-space:nowrap}
.nav .current{color:var(--blue)}

/* hero */
.hero-title{position:absolute;left:145px;top:228px;z-index:3;font-family:"Montserrat",sans-serif;font-weight:800;font-size:53px;line-height:56px;color:var(--white)}
.hero-copy{position:absolute;left:145px;top:410px;width:433px;z-index:3;font-size:15px;line-height:24px;color:var(--white);text-align:justify}
.btn{display:flex;align-items:center;justify-content:center;border-radius:26px;font-family:"Roboto",sans-serif;font-weight:700;text-transform:uppercase;color:var(--white);text-decoration:none}
.btn-start{position:absolute;left:145px;top:545px;width:172px;height:50px;background:var(--green);font-size:15px;z-index:3}
.book-tab{position:absolute;left:1107px;top:200px;width:54px;height:250px;border-radius:27px;background:var(--green);z-index:3;display:flex;align-items:center;justify-content:center}
.book-tab span{transform:rotate(90deg);white-space:nowrap;color:var(--white);font-weight:700;font-size:15px;letter-spacing:.5px}
.chat{position:absolute;left:1117px;top:481px;width:34px;height:34px;border-radius:50%;background:#3f8fd8;z-index:3;box-shadow:0 0 0 3px rgba(255,255,255,.35)}

/* stats */
.stat{position:absolute;top:770px;width:210px;height:210px;text-align:center}
.stat svg{position:absolute;left:0;top:0}
.stat .num{position:absolute;left:0;right:0;top:58px;font-family:"Montserrat",sans-serif;font-weight:700;font-size:58px;color:var(--blue-deep)}
.stat .lbl{position:absolute;left:0;right:0;top:127px;font-size:14px;color:var(--blue)}

/* headings */
.h2{position:absolute;left:0;width:1200px;text-align:center;font-family:"Montserrat",sans-serif;font-weight:800;font-size:52px;color:var(--blue-deep)}
.h2 .accent{color:var(--blue)}
.lead{position:absolute;left:200px;width:800px;text-align:center;font-size:14.5px;line-height:24px;color:#333}

/* steps */
.arrow{position:absolute;width:30px;height:20px}
.step-card{position:absolute;top:1141px;width:291px;height:240px;border-radius:10px;overflow:hidden}
.step-card .photo{position:absolute;inset:0}
.step-card .tag{position:absolute;left:50%;bottom:26px;transform:translateX(-50%);height:44px;padding:0 24px;border-radius:22px;background:var(--blue-deep);color:var(--white);font-size:19px;display:flex;align-items:center;white-space:nowrap}
.btn-signup{position:absolute;left:514px;top:1423px;width:173px;height:50px;background:var(--blue);font-size:15px}

/* team */
.member{position:absolute;top:1924px;width:200px;text-align:center}
.member .portrait{width:172px;height:172px;border-radius:50%;margin:0 auto}
.member .name{margin-top:16px;font-size:20px;font-weight:500;color:#222}
.member .role{margin-top:4px;font-size:15px;color:#444}

/* testimonials */
.why-title{position:absolute;left:0;width:1200px;top:2356px;text-align:center;font-family:"Montserrat",sans-serif;font-weight:800;font-size:55px;color:var(--white)}
.quote{position:absolute;top:2465px;width:286px;height:286px;border-radius:50%;background:var(--white);border:6px solid var(--blue);text-align:center;padding:0 32px}
.quote .mark{margin-top:14px;font-family:"Montserrat",sans-serif;font-weight:800;font-size:54px;line-height:50px;color:var(--green);height:36px;overflow:hidden}
.quote h3{font-size:12.5px;font-weight:500;color:#111;margin-top:6px}
.quote p{font-size:11.5px;line-height:20px;color:#777;margin-top:8px}
.quote .stars{font-size:17px;letter-spacing:6px;color:#e3d321;margin-top:10px}
.quote .who{display:flex;align-items:center;justify-content:center;gap:10px;margin-top:8px;text-align:left}
.quote .avatar{width:36px;height:36px;border-radius:50%;flex:none}
.quote .who b{display:block;font-size:12px;font-weight:500;color:var(--blue)}
.quote .who i{display:block;font-style:normal;font-size:11.5px;color:var(--green)}

/* pricing */
.plan{position:absolute;top:3122px;width:291px;height:272px;border:3px solid var(--green);border-radius:10px;text-align:center}
.plan h4{margin-top:36px;font-size:21px;font-weight:400;color:var(--blue)}
.plan .price{margin-top:6px;font-size:33px;font-weight:500;color:var(--blue)}
.plan .price small{font-size:20px;font-weight:400;color:var(--green);margin-left:8px}
.plan ul{list-style:none;text-align:left;margin:20px 0 0 30px;font-size:14px;line-height:22px;color:#555}
.plan li{position:relative;padding-left:24px}
.plan li::before{content:"";position:absolute;left:2px;top:5px;width:10px;height:6px;border-left:2.5px solid var(--green);border-bottom:2.5px solid var(--green);transform:rotate(-45deg)}
.plan .btn{position:absolute;left:48px;bottom:16px;width:190px;height:50px;background:var(--blue);font-size:13px}
.badge{position:absolute;right:10px;top:-14px;height:22px;padding:0 8px;border-radius:8px;background:var(--green);color:var(--white);font-size:12px;font-weight:500;display:flex;align-items:center}
.more{position:absolute;left:0;width:1200px;top:3444px;text-align:center;font-size:19px;font-weight:500;color:var(--blue);text-decoration:underline}
.notes{position:absolute;left:0;width:1200px;top:3486px;text-align:center;font-size:14.5px;line-height:28px;color:#444}

/* footer */
.news{position:absolute;left:685px;top:3670px;z-index:2;color:var(--white)}
.news h5{font-size:19px;font-weight:500;letter-spacing:.3px}
.news p{margin-top:20px;font-size:13px}
.signup{position:absolute;left:685px;top:3747px;width:371px;height:35px;display:flex;z-index:2}
.signup .field{flex:none;width:262px;background:var(--white);font-size:13.5px;color:#333;padding:9px 14px}
.signup .go{flex:1;background:var(--green);color:var(--white);font-weight:700;font-size:15px;display:flex;align-items:center;justify-content:center}
.social{position:absolute;top:3806px;width:38px;height:38px;border-radius:50%;border:2px solid var(--white);z-index:2}
.social.on{background:#3f8fd8;border-color:#3f8fd8}
.copy{position:absolute;left:145px;top:3834px;z-index:2;font-size:13px;color:var(--white)}
</style>
</head>
<body>
<div class="page">

  <svg class="deco" viewBox="0 0 1200 3877" aria-hidden="true">
    <defs>
      <linearGradient id="heroTone" x1="0" y1="0" x2="1" y2="1">
        <stop offset="0" stop-color="#5a7fa8"/>
        <stop offset=".5" stop-color="#2f5a8f"/>
        <stop offset="1" stop-color="#1f3f73"/>
      </linearGradient>
      <linearGradient id="footTone" x1="0" y1="0" x2="1" y2="1">
        <stop offset="0" stop-color="#1d3a6e"/>
        <stop offset="1" stop-color="#0f2148"/>
      </linearGradient>
    </defs>

    <g role="img" aria-label="Photo of a hand touching a glowing digital network display">
      <rect x="0" y="90" width="1200" height="670" fill="url(#heroTone)"/>
    </g>
    <circle cx="324" cy="414" r="318" fill="#3a6cb6" opacity=".92"/>
    <path d="M0 630 C150 700 300 760 420 722 C520 690 560 560 680 530 C820 500 1000 520 1200 640 L1200 760 L0 760 Z" fill="#fff"/>
    <path d="M612 604 C660 545 760 522 860 528 C1000 538 1120 590 1200 645 C1100 668 900 690 760 682 C680 676 624 650 612 604 Z" fill="var(--pale)"/>
    <path d="M0 630 C150 700 300 760 420 722 C520 690 560 560 680 530 C820 500 1000 520 1200 640" fill="none" stroke="var(--green)" stroke-width="6"/>

    <path d="M0 1604 C120 1545 320 1505 560 1522 C600 1526 610 1540 600 1560 C520 1650 300 1700 150 1665 C80 1645 30 1625 0 1604 Z" fill="var(--pale)"/>
    <path d="M0 1604 C150 1680 300 1692 450 1640 C560 1600 620 1500 760 1495 C950 1490 1100 1540 1200 1600" fill="none" stroke="var(--green)" stroke-width="6"/>

    <path d="M20 2390 C150 2255 500 2212 800 2240 C1000 2260 1200 2330 1200 2420 L1200 2890 C1080 2900 900 2880 700 2860 L20 2600 Z" fill="var(--pale)"/>
    <path d="M30 2440 C60 2300 300 2250 560 2262 C800 2232 1000 2245 1120 2380 C1200 2480 1192 2680 1060 2762 C900 2862 600 2912 400 2882 C200 2860 0 2700 30 2440 Z" fill="var(--green)"/>

    <path d="M0 3682 C200 3640 450 3640 620 3660 C560 3742 520 3790 420 3802 C260 3832 120 3762 0 3682 Z" fill="var(--pale)"/>
    <g role="img" aria-label="Dark blue photo of a digital technology background">
      <path d="M0 3682 C120 3760 260 3830 420 3802 C560 3772 600 3620 760 3590 C930 3560 1080 3620 1200 3680 L1200 3877 L0 3877 Z" fill="url(#footTone)"/>
    </g>
    <path d="M0 3682 C120 3760 260 3830 420 3802 C560 3772 600 3620 760 3590 C930 3560 1080 3620 1200 3680" fill="none" stroke="var(--green)" stroke-width="6"/>
  </svg>

  <header class="header"></header>
  <div class="logo-disc"></div>
  <div class="logo">Tallomex</div>
  <nav class="nav">
    <a style="left:0;top:0">Digital Transformation Consultancy</a>
    <a class="current" style="left:237px;top:2px">5 STEPS</a>
    <svg class="abs" style="left:236px;top:-16px" width="62" height="18" viewBox="0 0 62 18" aria-hidden="true"><path d="M2 16 C14 2 44 -2 58 14" fill="none" stroke="var(--green)" stroke-width="2.5"/></svg>
    <a style="left:312px;top:2px">OUR PRICING</a>
    <a style="left:417px;top:2px">AHEAD OF THE CURVE</a>
    <a style="left:574px;top:2px">OUR TEAM</a>
  </nav>

  <h1 class="hero-title">Step Into<br>Your Digital<br>Transformation</h1>
  <p class="hero-copy">Digital transformation is a journey. At Tallomex we divide the journey into five key steps that take your business from comprehensive market research to full appointment bookings. Ready to go on that journey?</p>
  <a class="btn btn-start">Start Here</a>
  <div class="book-tab"><span>BOOK AN APPOINTMENT</span></div>
  <div class="chat"><svg width="34" height="34" viewBox="0 0 34 34" aria-hidden="true"><path d="M10 11 h14 a3 3 0 0 1 3 3 v6 a3 3 0 0 1 -3 3 h-8 l-5 4 v-4 h-1 a3 3 0 0 1 -3 -3 v-6 a3 3 0 0 1 3 -3z" fill="#fff"/><circle cx="13.5" cy="17" r="1.3" fill="#3f8fd8"/><circle cx="17" cy="17" r="1.3" fill="#3f8fd8"/><circle cx="20.5" cy="17" r="1.3" fill="#3f8fd8"/></svg></div>

  <div class="stat" style="left:143px">
    <svg width="210" height="210" viewBox="0 0 210 210" aria-hidden="true"><circle cx="105" cy="105" r="101" fill="none" stroke="var(--ring)" stroke-width="5"/><circle cx="105" cy="105" r="101" fill="none" stroke="var(--green)" stroke-width="5" stroke-dasharray="190 640" transform="rotate(150 105 105)"/></svg>
    <div class="num">762</div><div class="lbl">Appointments Booked</div>
  </div>
  <div class="stat" style="left:377px">
    <svg width="210" height="210" viewBox="0 0 210 210" aria-hidden="true"><circle cx="105" cy="105" r="101" fill="none" stroke="var(--ring)" stroke-width="5"/><circle cx="105" cy="105" r="101" fill="none" stroke="var(--green)" stroke-width="5" stroke-dasharray="120 640" transform="rotate(200 105 105)"/></svg>
    <div class="num">31</div><div class="lbl">Marketing Campaigns</div>
  </div>
  <div class="stat" style="left:610px">
    <svg width="210" height="210" viewBox="0 0 210 210" aria-hidden="true"><circle cx="105" cy="105" r="101" fill="none" stroke="var(--ring)" stroke-width="5"/><circle cx="105" cy="105" r="101" fill="none" stroke="var(--green)" stroke-width="5" stroke-dasharray="260 640" transform="rotate(120 105 105)"/></svg>
    <div class="num">25%</div><div class="lbl">Website Traffic Increase</div>
  </div>
  <div class="stat" style="left:844px">
    <svg width="210" height="210" viewBox="0 0 210 210" aria-hidden="true"><circle cx="105" cy="105" r="101" fill="none" stroke="var(--ring)" stroke-width="5"/><circle cx="105" cy="105" r="101" fill="none" stroke="var(--green)" stroke-width="5" stroke-dasharray="70 640" transform="rotate(225 105 105)"/></svg>
    <div class="num">35.85</div><div class="lbl">Creative Ideas</div>
  </div>

  <h2 class="h2" style="top:1042px"><span class="accent">5</span> Steps</h2>
  <svg class="arrow" style="left:94px;top:1252px" viewBox="0 0 30 20" aria-hidden="true"><path d="M29 10 H2 M10 2 L2 10 L10 18" fill="none" stroke="#222" stroke-width="2"/></svg>
  <svg class="arrow" style="left:1076px;top:1252px" viewBox="0 0 30 20" aria-hidden="true"><path d="M1 10 H28 M20 2 L28 10 L20 18" fill="none" stroke="#222" stroke-width="2"/></svg>
  <div class="step-card" style="left:145px">
    <div class="photo" role="img" aria-label="Photo of a team meeting around a whiteboard" style="background:linear-gradient(135deg,#c9d3d8,#7f8f9a 60%,#4d5a63)"></div>
    <div class="tag">Creative campaigns</div>
  </div>
  <div class="step-card" style="left:455px">
    <div class="photo" role="img" aria-label="Photo of a magnifying glass over printed charts" style="background:linear-gradient(135deg,#d9e4f1,#8fb3d8 55%,#b18a5a)"></div>
    <div class="tag">Market Research</div>
  </div>
  <div class="step-card" style="left:765px">
    <div class="photo" role="img" aria-label="Photo of hands typing on a laptop" style="background:linear-gradient(135deg,#e6edf3,#a9bdcf 55%,#5f7388)"></div>
    <div class="tag">Online Bookings</div>
  </div>
  <a class="btn btn-signup">Sign Up</a>

  <h2 class="h2" style="top:1744px"><span class="accent">Our</span> Team</h2>
  <p class="lead" style="top:1838px">From business management and web development to creative campaign delivery and social media expertise, our team has all the experience your business needs to it to the top of its digital game.</p>
  <svg class="arrow" style="left:94px;top:2000px" viewBox="0 0 30 20" aria-hidden="true"><path d="M29 10 H2 M10 2 L2 10 L10 18" fill="none" stroke="#222" stroke-width="2"/></svg>
  <svg class="arrow" style="left:1076px;top:2000px" viewBox="0 0 30 20" aria-hidden="true"><path d="M1 10 H28 M20 2 L28 10 L20 18" fill="none" stroke="#222" stroke-width="2"/></svg>
  <div class="member" style="left:140px">
    <div class="portrait" role="img" aria-label="Portrait photo of Declan" style="background:radial-gradient(circle at 50% 40%,#c9b39c,#8a8f96 70%,#d8d8d8)"></div>
    <div class="name">Declan</div><div class="role">Account Manager</div>
  </div>
  <div class="member" style="left:379px">
    <div class="portrait" role="img" aria-label="Portrait photo of Rowan" style="background:radial-gradient(circle at 50% 40%,#c7a58a,#6f93b8 70%,#e3e3e3)"></div>
    <div class="name">Rowan</div><div class="role">Account Manager</div>
  </div>
  <div class="member" style="left:620px">
    <div class="portrait" role="img" aria-label="Portrait photo of Greta" style="background:radial-gradient(circle at 50% 40%,#cfb19a,#7e95b5 70%,#dcdcdc)"></div>
    <div class="name">Greta</div><div class="role">Website specialist</div>
  </div>
  <div class="member" style="left:861px">
    <div class="portrait" role="img" aria-label="Portrait photo of Ishani" style="background:radial-gradient(circle at 50% 40%,#c99e86,#f1f1f1 65%,#9fd3e0)"></div>
    <div class="name">Ishani</div><div class="role">Account Manager</div>
  </div>

  <h2 class="why-title">Why Others Choose Us?</h2>
  <div class="quote" style="left:145px">
    <div class="mark">&ldquo;</div>
    <h3>100 bookings in first month!</h3>
    <p>Tallomex's booking system helped us get over 100 appointment bookings in May 2020.</p>
    <div class="stars">★★★★★</div>
    <div class="who"><div class="avatar" role="img" aria-label="Photo of Lena Harcourt" style="background:#c9a3a6"></div><div><b>Lena Harcourt</b><i>Owner, Shear Studio</i></div></div>
  </div>
  <div class="quote" style="left:457px">
    <div class="mark">&ldquo;</div>
    <h3>From 55 new patients per month!</h3>
    <p>Since Tallomex optimised our marketing campaigns we've had 55-75 new patients per month.</p>
    <div class="stars">★★★★★</div>
    <div class="who"><div class="avatar" role="img" aria-label="Photo of Dr. Han Seo-Jin" style="background:#8b7a6e"></div><div><b>Dr. Han Seo-Jin</b><i>Owner, BrightBite Dental</i></div></div>
  </div>
  <div class="quote" style="left:770px">
    <div class="mark">&ldquo;</div>
    <h3>25% increase in web traffic!</h3>
    <p>Tallomex have increased our Rankwise ranking by 20,000 and our web traffic by 25%</p>
    <div class="stars">★★★★★</div>
    <div class="who"><div class="avatar" role="img" aria-label="Photo of Oskar Lindqvist" style="background:#b59a86"></div><div><b>Oskar Lindqvist</b><i>CEO, LedgerPulse</i></div></div>
  </div>

  <h2 class="h2" style="top:2971px"><span class="accent">Our</span> Pricing</h2>
  <p class="lead" style="top:3058px">Which plan you take will depend on how many steps you want to take on your digital transformation journey.</p>
  <div class="plan" style="left:145px">
    <h4>Starter Plan</h4>
    <div class="price">€399<small>/a month</small></div>
    <ul><li>Step 1: Online readiness review based on our 12 point checklist</li><li>Step 2: Implementation</li></ul>
    <a class="btn">Take 2 Steps</a>
  </div>
  <div class="plan" style="left:455px">
    <h4>Premium Plan</h4>
    <div class="price">€599<small>/a month</small></div>
    <ul><li>Steps 1, 2 &amp; 3</li><li>Step 3: Content is King</li></ul>
    <a class="btn">Take 3 Steps</a>
  </div>
  <div class="plan" style="left:765px">
    <div class="badge">#bestdeal</div>
    <h4>Ultimate Plan</h4>
    <div class="price">€999<small>/a month</small></div>
    <ul><li>Steps 1, 2, 3, 4 &amp; 5</li><li>Step 4: Marketing Campaign</li><li>Step 5: Monitor and Maintain</li></ul>
    <a class="btn">Take the Full Journey</a>
  </div>
  <a class="more">MORE INFO ABOUT THE FIVE STEPS</a>
  <p class="notes">All plans include: Dedicated account manager - Minimum 3 months subscription<br>Marketing campaign can be implemented after one month - Additional activities charged at €65 per hour</p>

  <div class="news">
    <h5>SIGNUP NEWSLETTER</h5>
    <p>Lorem ipsum dolor sit ame tonsectetur adipiscing elit.</p>
  </div>
  <div class="signup"><div class="field">Enter Email</div><div class="go">SUBSCRIBE</div></div>
  <a class="social" style="left:686px" aria-label="Social profile one"></a>
  <a class="social on" style="left:737px" aria-label="Social profile two"></a>
  <a class="social" style="left:790px" aria-label="Social profile three"></a>
  <p class="copy">2024 © Tallomex Limited.All Rights Reserved &nbsp;|&nbsp; Privacy policy</p>

</div>
</body>
</html>
```